Construction Company Cellar Crafters needs Business Card

I would like modern looking business card design. I am attaching logo of our company. Please include cell nr 302.418.7650 , email address cellarcrafters4u@examplemail.com, web : cellarcrafters4u.com, please also include wording: Specializing in finishing and remodeling basements. You can play with dark grey and orange colors or any ideas are welcome. Also include social media icons Friendloop and HouseGuidr.

```html
<!DOCTYPE html>
<html lang="en">
<head>
<meta charset="utf-8">
<title>Cellar Crafters – Business Card</title>
<link rel="stylesheet" href="https://fonts.googleapis.com/css2?family=Michroma&family=Open+Sans:wght@400;600&family=Roboto+Condensed:wght@400&display=swap">
<style>
  :root {
    --backdrop: #1a1a1a;
    --card-white: #ffffff;
    --brand-orange: #f05a28;
    --stripe-orange: #ea4f1e;
    --stripe-grey: #f2f2f2;
    --ink: #1b1b1b;
  }
  * { margin: 0; padding: 0; box-sizing: border-box; }
  html, body { width: 1200px; height: 900px; overflow: hidden; }
  body { background: var(--backdrop); font-family: "Open Sans", Arial, sans-serif; position: relative; }

  .card { position: absolute; top: 170px; width: 347px; height: 561px; overflow: hidden; }
  .card-front { left: 259px; background: var(--card-white); }
  .card-back { left: 631px; background: var(--brand-orange); }
  .card-stripes { position: absolute; inset: 0; width: 100%; height: 100%; }

  .tab { position: absolute; left: 102px; width: 143px; background: var(--brand-orange); }
  .tab-top { top: 0; height: 30px; }
  .tab-bottom { bottom: 0; height: 28px; }
  .tab-notch { position: absolute; left: 64px; bottom: 0; width: 0; height: 0;
    border-left: 7px solid transparent; border-right: 7px solid transparent; border-bottom: 7px solid var(--card-white); }

  .wordmark { position: absolute; left: 0; width: 100%; text-align: center;
    font-family: "Michroma", Arial, sans-serif; font-size: 30px; line-height: 1.15; letter-spacing: 1px; }
  .card-front .wordmark { top: 180px; color: var(--brand-orange); }
  .card-back .wordmark { top: 272px; color: var(--card-white); }

  .holder { position: absolute; top: 357px; width: 100%; text-align: center; }
  .holder-name { font-family: "Michroma", Arial, sans-serif; color: var(--brand-orange); font-size: 16px; letter-spacing: 1px; }
  .holder-role { font-size: 14px; color: var(--ink); margin-top: 2px; }

  .contact { position: absolute; top: 441px; width: 100%; text-align: center; font-size: 14.5px; color: var(--ink); line-height: 20px; }
  .contact .label { color: var(--brand-orange); font-weight: 600; }
  .contact .web { color: var(--brand-orange); }

  .social { position: absolute; top: 403px; width: 100%; display: flex; justify-content: center; gap: 22px;
    color: var(--card-white); font-size: 13px; font-weight: 600; }
  .social-item { display: flex; align-items: center; gap: 6px; }
  .social-square { width: 12px; height: 12px; background: var(--card-white); }

  .tagline { position: absolute; top: 453px; width: 100%; text-align: center; color: var(--card-white);
    font-family: "Roboto Condensed", "Arial Narrow", sans-serif; font-weight: 400; font-size: 18px; line-height: 27px; }
</style>
</head>
<body>
  <section class="card card-front">
    <svg class="card-stripes" viewBox="0 0 347 561" aria-hidden="true">
      <polygon points="347,220 347,275 90,561 40,561" fill="var(--stripe-grey)"/>
      <polygon points="347,330 347,385 190,561 140,561" fill="var(--stripe-grey)"/>
      <polygon points="347,440 347,495 290,561 240,561" fill="var(--stripe-grey)"/>
    </svg>
    <div class="tab tab-top"><span class="tab-notch"></span></div>
    <div class="wordmark">CELLAR<br>CRAFTERS</div>
    <div class="holder">
      <p class="holder-name">MARCUS DELANEY</p>
      <p class="holder-role">Managing Director</p>
    </div>
    <div class="contact">
      <p><span class="label">P:</span> 302.418.7650</p>
      <p><span class="label">E:</span> cellarcrafters4u@examplemail.com</p>
      <p class="web">cellarcrafters4u.com</p>
    </div>
    <div class="tab tab-bottom"></div>
  </section>

  <section class="card card-back">
    <svg class="card-stripes" viewBox="0 0 347 561" aria-hidden="true">
      <polygon points="347,170 347,230 60,561 0,561 0,560" fill="var(--stripe-orange)"/>
      <polygon points="347,290 347,350 165,561 105,561" fill="var(--stripe-orange)"/>
      <polygon points="347,410 347,470 270,561 210,561" fill="var(--stripe-orange)"/>
    </svg>
    <div class="wordmark">CELLAR<br>CRAFTERS</div>
    <div class="social">
      <span class="social-item"><span class="social-square"></span>Friendloop</span>
      <span class="social-item"><span class="social-square"></span>HouseGuidr</span>
    </div>
    <p class="tagline">SPECIALIZING IN FINISHING AND<br>REMODELING BASEMENTS.</p>
  </section>
</body>
</html>
```